Coffee Bag Design for Tollbury Coffee

We’re excited to invite you to help us bring Tollbury Coffee to life on grocery store shelves with a design that embodies our mission of spreading goodness and creating a lasting impact. Tollbury Coffee represents warmth, positivity, and the power of small actions to create ripples of goodness. Each cup not only offers a rich, gourmet coffee experience but also gives back to the community, with $2 from each bag supporting local food banks.

To reflect this vision, we’d love for the design to feature a dark (greyish) blue as the base color to convey depth and quality, complemented by a vibrant light blue that will catch the eye and add energy. Tan or gold accents could add an elegant touch and a feeling of warmth. We are aiming for a look that feels uplifting and engaging, with simplicity and elegance, yet stands out amid other brands on the shelf.

I am attaching the dimension of the bag.

Other information that needs to be listed:
Ingredients: 100% Arabica Coffee
Net Wt. 12 oz. (340 g)
Roasted and distributed by:
Name
Address
email

Text on the back of the bag:
Tollbury Coffee is crafted with a belief that kindness and positivity can spread, touching countless lives with every sip. This gourmet blend delivers a rich taste experience while giving back, as $2 from each bag sold is donated to local food banks to help those in need. Enjoy the warmth and goodness in each cup, knowing you’re making a difference with every purchase.

Thank you!

```html
<!DOCTYPE html>
<html lang="en">
<head>
<meta charset="UTF-8">
<title>Tollbury Coffee – Bag Dieline</title>
<link rel="stylesheet" href="https://fonts.googleapis.com/css2?family=Bree+Serif&family=Montserrat:wght@300;400;500;700&family=Satisfy&display=swap">
<style>
  :root {
    --navy: #28334a;
    --navy-deep: #232b3c;
    --gold: #d4ae36;
    --sky: #b5dcf2;
    --dieline: #e0303a;
    --dim-blue: #3e5fb0;
    --paper: #ffffff;
    --ink: #1f2430;
    --soft-text: #d6dbe4;
    --note-grey: #c3c8d2;
  }
  * { box-sizing: border-box; margin: 0; padding: 0; }
  html, body { width: 1200px; height: 1000px; overflow: hidden; background: var(--paper); }
  .sheet { position: relative; width: 1200px; height: 1000px; font-family: "Montserrat", sans-serif; }

  .panel {
    position: absolute;
    background: linear-gradient(135deg, var(--navy-deep) 0%, var(--navy) 55%, var(--navy-deep) 100%);
    border: 1px solid var(--dieline);
    border-radius: 9px;
    overflow: hidden;
  }
  .panel-left  { left: 60px;  top: 221px; width: 181px; height: 408px; }
  .panel-front { left: 241px; top: 221px; width: 341px; height: 408px; }
  .panel-right { left: 582px; top: 221px; width: 182px; height: 408px; }
  .panel-back  { left: 764px; top: 221px; width: 341px; height: 408px; }
  .panel-base  { left: 241px; top: 629px; width: 341px; height: 182px; }

  .safe-line {
    position: absolute; inset: 0 14px 14px 14px;
    border-left: 1px dashed rgba(255,255,255,.55);
    border-right: 1px dashed rgba(255,255,255,.55);
    border-bottom: 1px dashed rgba(255,255,255,.55);
    pointer-events: none;
  }
  .panel-base .safe-line { inset: 14px; border: 1px dashed rgba(255,255,255,.55); }

  .brand-mark {
    position: absolute; display: flex; align-items: center; gap: 5px;
    color: var(--gold); font-family: "Montserrat", sans-serif; font-weight: 500;
    white-space: nowrap; transform: translateX(-50%);
  }
  .brand-mark .dot { border: 1.5px solid var(--gold); border-radius: 50%; }
  .mark-top  { left: 170px; top: 38px; font-size: 11px; }
  .mark-top .dot { width: 10px; height: 10px; }
  .mark-side { top: 290px; font-size: 11px; }
  .mark-side .dot { width: 10px; height: 10px; }
  .panel-left .mark-side  { left: 90px; }
  .panel-right .mark-side { left: 91px; }
  .mark-base { left: 170px; top: 76px; font-size: 24px; gap: 10px; }
  .mark-base .dot { width: 20px; height: 20px; border-width: 2px; }

  .label-frame {
    position: absolute; left: 72px; top: 86px; width: 197px; height: 287px;
    border: 1.5px solid var(--sky); border-radius: 6px;
  }
  .title-band {
    position: absolute; left: 0; top: 120px; width: 100%; height: 85px;
    background: var(--gold); text-align: center;
    font-family: "Bree Serif", serif; color: var(--ink);
    font-size: 37px; line-height: 36px; padding-top: 7px;
  }
  .origin {
    position: absolute; left: 0; width: 100%; top: 210px; text-align: center;
    color: #fff; font-size: 9.5px; font-weight: 500; letter-spacing: 1.6px;
  }
  .cup-art {
    position: absolute; left: 88px; top: 228px; width: 165px; height: 130px;
    background: radial-gradient(ellipse at center, rgba(212,174,54,.35) 0%, rgba(181,220,242,.12) 45%, transparent 75%);
  }
  .net-weight {
    position: absolute; left: 0; width: 100%; top: 381px; text-align: center;
    color: #fff; font-size: 6.5px; font-weight: 700; letter-spacing: .5px;
  }
  .net-weight strong { font-size: 13px; letter-spacing: 1px; }

  .zipper-zone { position: absolute; left: 0; top: 54px; width: 100%; height: 51px; }
  .tear-guide { position: absolute; left: 0; top: 0; }

  .back-heading {
    position: absolute; left: 0; width: 100%; top: 220px; text-align: center;
    font-family: "Satisfy", cursive; font-weight: 400; color: var(--gold); font-size: 19px;
  }
  .back-heading::after {
    content: ""; display: block; width: 150px; height: 1px; margin: 1px auto 0;
    background: rgba(212,174,54,.5);
  }
  .mission-box {
    position: absolute; left: 30px; top: 256px; width: 280px; height: 87px;
    border: 1.5px solid var(--sky); padding: 11px 13px;
    color: var(--soft-text); font-size: 7.6px; font-weight: 300; line-height: 9.6px;
    letter-spacing: .55px; text-align: justify; text-align-last: left;
  }
  .roaster {
    position: absolute; left: 0; width: 100%; top: 366px; text-align: center;
    color: var(--soft-text); font-size: 7.6px; font-weight: 300; line-height: 9.8px; letter-spacing: .3px;
  }
  .roaster strong { font-weight: 700; color: #fff; }

  .dims { position: absolute; left: 0; top: 0; width: 1200px; height: 1000px; pointer-events: none; }
  .dim-name, .dim-size {
    position: absolute; font-size: 12px; font-weight: 300; transform: translateX(-50%);
    background: var(--paper); padding: 0 3px; white-space: nowrap;
  }
  .dim-name { color: var(--dieline); top: 186px; }
  .dim-size { color: var(--dim-blue); top: 203px; }
  .dim-vert { position: absolute; color: var(--dim-blue); font-size: 12px; font-weight: 300;
    transform: translate(-50%, -50%) rotate(-90deg); background: var(--paper); padding: 0 3px; white-space: nowrap; }
  .dim-small { position: absolute; color: var(--note-grey); font-size: 10px; font-weight: 300; white-space: nowrap; }
  .dim-small.vertical { transform: translate(-50%, -50%) rotate(-90deg); }
  .zipper-note { position: absolute; left: 1120px; top: 305px; color: var(--dim-blue); font-size: 12px; font-weight: 300; }
</style>
</head>
<body>
<div class="sheet">

  <section class="panel panel-left">
    <div class="safe-line"></div>
    <div class="brand-mark mark-side"><span class="dot"></span>Tollbury Coffee</div>
  </section>

  <section class="panel panel-front">
    <div class="safe-line"></div>
    <div class="brand-mark mark-top"><span class="dot"></span>Tollbury Coffee</div>
    <div class="label-frame"></div>
    <div class="title-band">Tollbury<br>Coffee</div>
    <div class="origin">100% ARABICA COFFEE</div>
    <div class="cup-art" role="img" aria-label="Line illustration of a steaming coffee cup on a saucer with radiating rays"></div>
    <div class="net-weight">NET WT. <strong>12 OZ.</strong> (340 G)</div>
  </section>

  <section class="panel panel-right">
    <div class="safe-line"></div>
    <div class="brand-mark mark-side"><span class="dot"></span>Tollbury Coffee</div>
  </section>

  <section class="panel panel-back">
    <div class="safe-line"></div>
    <svg class="zipper-zone" viewBox="0 0 341 51" width="341" height="51" aria-hidden="true">
      <rect x="21" y="0" width="320" height="51" fill="rgba(212,174,54,.18)"/>
      <path d="M0 -2 H14 Q20 8 12 18 Q20 30 14 40 H0 Z" fill="rgba(212,174,54,.3)" stroke="rgba(224,48,58,.6)" stroke-width=".6"/>
      <rect x="21" y="12" width="320" height="2" fill="var(--gold)"/>
      <rect x="21" y="23" width="320" height="2" fill="var(--gold)"/>
      <rect x="21" y="32" width="320" height="7" fill="var(--gold)"/>
    </svg>
    <svg class="tear-guide" viewBox="0 0 341 220" width="341" height="220" aria-hidden="true">
      <line x1="171" y1="2" x2="171" y2="178" stroke="var(--gold)" stroke-width="1"/>
      <path d="M167 172 L171 179 L175 172" fill="none" stroke="var(--gold)" stroke-width="1"/>
      <path d="M168 6 L171 1 L174 6" fill="var(--dim-blue)"/>
      <circle cx="171" cy="182" r="25" fill="none" stroke="var(--gold)" stroke-width="1"/>
      <line x1="157" y1="182" x2="185" y2="182" stroke="var(--gold)" stroke-width="1"/>
    </svg>
    <h2 class="back-heading">Crafted with Kindness</h2>
    <p class="mission-box">Tollbury Coffee is crafted with a belief that kindness and positivity can spread, touching countless lives with every sip. This gourmet blend delivers a rich taste experience while giving back, as $2 from each bag sold is donated to local food banks to help those in need. Enjoy the warmth and goodness in each cup, knowing you’re making a difference with every purchase.</p>
    <p class="roaster">Roasted and distributed by: <strong>Marlowe Roasters</strong><br>88 Harbor Lane, City, State, 12345<br>Email: <strong>info@tollburycoffee.com</strong></p>
  </section>

  <section class="panel panel-base">
    <div class="safe-line"></div>
    <div class="brand-mark mark-base"><span class="dot"></span>Tollbury Coffee</div>
  </section>

  <div class="dims">
    <svg width="1200" height="1000" viewBox="0 0 1200 1000" aria-hidden="true">
      <g stroke="var(--dieline)" stroke-width="1" fill="none">
        <line x1="241" y1="209" x2="582" y2="209"/>
        <line x1="582" y1="209" x2="764" y2="209"/>
        <line x1="764" y1="209" x2="1105" y2="209"/>
        <line x1="241" y1="202" x2="241" y2="221"/>
        <line x1="582" y1="202" x2="582" y2="221"/>
        <line x1="764" y1="202" x2="764" y2="221"/>
        <line x1="1105" y1="202" x2="1105" y2="221"/>
        <path d="M247 205 L241 209 L247 213 M576 205 L582 209 L576 213 M588 205 L582 209 L588 213 M758 205 L764 209 L758 213 M770 205 L764 209 L770 213 M1099 205 L1105 209 L1099 213"/>
        <line x1="48" y1="629" x2="48" y2="811"/>
        <line x1="41" y1="629" x2="60" y2="629"/>
        <line x1="41" y1="811" x2="68" y2="811"/>
        <path d="M44 635 L48 629 L52 635 M44 805 L48 811 L52 805"/>
        <line x1="60" y1="609" x2="75" y2="609"/>
        <line x1="97" y1="615" x2="97" y2="629"/>
      </g>
      <g stroke="var(--ink)" stroke-width=".8">
        <line x1="1111" y1="221" x2="1133" y2="221"/>
        <line x1="1105" y1="289" x2="1133" y2="289"/>
        <line x1="1111" y1="221" x2="1111" y2="289"/>
        <line x1="1105" y1="298" x2="1112" y2="309"/>
      </g>
    </svg>
    <span class="dim-name" style="left:154px">Left</span>
    <span class="dim-size" style="left:153px">80 mm</span>
    <span class="dim-name" style="left:438px">Front</span>
    <span class="dim-size" style="left:441px">150 mm</span>
    <span class="dim-name" style="left:671px">Right</span>
    <span class="dim-size" style="left:676px">80 mm</span>
    <span class="dim-name" style="left:905px">Back</span>
    <span class="dim-size" style="left:907px">150 mm</span>
    <span class="dim-vert" style="left:50px; top:449px">180 mm</span>
    <span class="dim-vert" style="left:48px; top:720px">80 mm</span>
    <span class="dim-vert" style="left:1124px; top:254px">30mm</span>
    <span class="dim-small" style="left:102px; top:615px">6.5mm</span>
    <span class="dim-small vertical" style="left:68px; top:584px">6.5mm</span>
    <span class="zipper-note">Zipper</span>
  </div>

</div>
</body>
</html>
```